BuildLinkHub.com Full Stationery Design

Business Card will have all info on it. Letterhead will not have name, title or mobile number. Keep general feeling very clean, using colors from the logo as accents.
Name:Dale Marchetti
Title:President
Phone: 1-800-555-0142
Cell: 306-555-0187
email: dale@buildlinkhub.example
website: www.buildlinkhub.example
Address:
PO Box 947
Ridgeford, SK
S0J2T0

Target Market(s)

Construction Business owners

Industry/Entity Type

Business

Contact Information for Business Card

Name:Dale Marchetti
Title:President
Phone: 1-800-555-0142
Cell: 306-555-0187
Address:
PO Box 947
Ridgeford, SK
S0J2T0

Font styles to use
Sans Serif

Requirements
Must have
• Clean look
Should not have
• Images or cartoon type characters or tools

```html
<!DOCTYPE html>
<html lang="en">
<head>
<meta charset="utf-8">
<title>BuildLinkHub.com Business Card</title>
<link rel="stylesheet" href="https://fonts.googleapis.com/css2?family=Open+Sans:wght@400;600;700&display=swap">
<style>
  :root {
    --backdrop: #5a4a3b;
    --card-white: #ffffff;
    --slate: #4a5a6c;
    --slate-light: #6c8192;
    --slate-text: #465364;
    --accent-orange: #f26a21;
    --accent-red: #e8262b;
    --body-grey: #4d4d4d;
  }
  * { margin: 0; padding: 0; box-sizing: border-box; }
  html, body {
    width: 1200px; height: 987px; overflow: hidden;
    background: var(--backdrop);
    font-family: "Open Sans", Arial, sans-serif;
  }
  .stage { position: relative; width: 1200px; height: 987px; }
  .card {
    position: absolute; width: 615px; height: 352px;
    background: var(--card-white);
    box-shadow: 0 3px 8px rgba(0,0,0,0.35);
    overflow: hidden;
  }
  .card-front { left: 293px; top: 130px; }
  .card-back { left: 292px; top: 505px; }

  .front-band { position: absolute; inset: 0; width: 615px; height: 352px; }

  .brand {
    position: absolute; display: flex; align-items: center; gap: 12px;
    color: var(--slate-text); font-weight: 700; letter-spacing: 0.2px;
  }
  .brand-square { width: 22px; height: 22px; background: var(--accent-orange); }
  .card-front .brand { left: 0; right: 0; top: 62px; justify-content: center; font-size: 32px; }
  .card-back .brand { left: 0; right: 0; top: 148px; justify-content: center; font-size: 40px; }
  .card-back .brand-square { width: 28px; height: 28px; }

  .holder { position: absolute; left: 0; right: 0; top: 165px; text-align: center; }
  .holder-name { font-size: 22px; font-weight: 700; color: var(--slate-text); line-height: 1.2; }
  .holder-title { font-size: 16px; color: var(--accent-orange); line-height: 1.3; }

  .contact {
    position: absolute; top: 262px; list-style: none;
    color: #ffffff; font-size: 16px; line-height: 23px;
  }
  .contact-left { left: 28px; }
  .contact-left li { display: flex; align-items: center; gap: 8px; }
  .contact-left svg { width: 14px; height: 14px; flex: none; }
  .contact-right { right: 28px; text-align: right; }

  .back-url {
    position: absolute; left: 0; right: 0; top: 290px;
    text-align: center; font-size: 17px; color: var(--body-grey);
  }
</style>
</head>
<body>
<main class="stage">
  <section class="card card-front">
    <svg class="front-band" viewBox="0 0 615 352" aria-hidden="true">
      <defs>
        <radialGradient id="bandGlow" cx="50%" cy="80%" r="65%">
          <stop offset="0" stop-color="#6c8192"/>
          <stop offset="1" stop-color="#4a5a6c"/>
        </radialGradient>
        <linearGradient id="accentLine" x1="0" x2="1">
          <stop offset="0" stop-color="#e8262b"/>
          <stop offset="0.5" stop-color="#f26a21"/>
          <stop offset="1" stop-color="#e8262b"/>
        </linearGradient>
      </defs>
      <polygon points="0,96 150,246 465,246 615,94 615,352 0,352" fill="url(#bandGlow)"/>
      <polyline points="0,89 153,240 462,240 615,87" fill="none" stroke="url(#accentLine)" stroke-width="3"/>
    </svg>

    <div class="brand"><span class="brand-square"></span><span>BuildLinkHub.com</span></div>

    <div class="holder">
      <p class="holder-name">Dale Marchetti</p>
      <p class="holder-title">President</p>
    </div>

    <ul class="contact contact-left">
      <li><svg viewBox="0 0 16 16"><path fill="#fff" d="M3.6 1.2l2.3 2.6-1.3 1.9c.9 2 2.6 3.8 4.7 4.8l1.9-1.3 2.6 2.3-1.4 2.6C7.8 14 2 8.2 1 3z"/></svg>1-800-555-0142</li>
      <li><svg viewBox="0 0 16 16"><rect x="4" y="1" width="8" height="14" rx="1.5" fill="none" stroke="#fff" stroke-width="1.6"/><circle cx="8" cy="12.5" r="0.9" fill="#fff"/></svg>306-555-0187</li>
      <li><svg viewBox="0 0 16 16"><rect x="1" y="3.5" width="14" height="9" fill="#fff"/><polyline points="1,3.5 8,9 15,3.5" fill="none" stroke="#4a5a6c" stroke-width="1.2"/></svg>dale@buildlinkhub.example</li>
    </ul>

    <ul class="contact contact-right">
      <li>PO Box 947</li>
      <li>Ridgeford, SK, S0J2T0</li>
      <li>www.buildlinkhub.example</li>
    </ul>
  </section>

  <section class="card card-back">
    <div class="brand"><span class="brand-square"></span><span>BuildLinkHub.com</span></div>
    <p class="back-url">www.buildlinkhub.example</p>
  </section>
</main>
</body>
</html>
```